Business card for law firm

Need business card for new law firm. Think confident, authoritative, conservative, but not stuffy or old-fashioned.

Contact Information for Business Card

Content for card - logo (uploaded), plus the following:

Paul Whitcombe (larger font)
Managing Partner (larger font, but not as large as name)
Level 9, 7 Ferris Lane
Sydney NSW 2000
Main Tel 02 9364 2710
Direct Tel 02 8472 3159
Email paul@qvlegal.com.au
www.qvlegal.com.au

Letterhead design should include logo plus:
Level 9, 7 Ferris Lane
Sydney NSW 2000
Tel 02 8472 3159
www.qvlegal.com.au

```html
<!DOCTYPE html>
<html lang="en">
<head>
<meta charset="utf-8">
<title>Quayvale Lawyers – Business Card</title>
<link rel="stylesheet" href="https://fonts.googleapis.com/css2?family=Open+Sans:wght@400;600;700&display=swap">
<style>
  :root {
    --navy: #001c54;
    --ink: #0a0a0a;
    --white: #ffffff;
    --backdrop-top: #ececec;
    --backdrop-bottom: #c9cacc;
    --text-dark: #1a1a1a;
  }
  html, body {
    margin: 0;
    padding: 0;
    width: 1200px;
    height: 1113px;
    overflow: hidden;
  }
  body {
    position: relative;
    background: linear-gradient(160deg, var(--backdrop-top), var(--backdrop-bottom));
    font-family: "Open Sans", Arial, sans-serif;
  }
  .card {
    position: absolute;
    width: 769px;
    height: 440px;
    border-radius: 28px;
    overflow: hidden;
  }
  .card--front {
    left: 357px;
    top: 73px;
    background: var(--white);
    box-shadow: 0 0 0 1px #b8b8b8;
  }
  .card--back {
    left: 61px;
    top: 581px;
    background: var(--navy);
  }
  .card__art {
    position: absolute;
    inset: 0;
  }
  .wordmark {
    position: absolute;
    display: flex;
    align-items: center;
    gap: 14px;
    font-weight: 600;
    font-size: 34px;
    letter-spacing: 4px;
    text-transform: uppercase;
    white-space: nowrap;
  }
  .wordmark__square {
    width: 26px;
    height: 26px;
    background: currentColor;
  }
  .card--front .wordmark {
    left: 48px;
    top: 150px;
    color: var(--navy);
  }
  .card--back .wordmark {
    left: 36px;
    top: 86px;
    color: var(--white);
  }
  .person {
    position: absolute;
    left: 49px;
    top: 254px;
  }
  .person__name {
    margin: 0;
    font-weight: 700;
    font-size: 27px;
    color: var(--navy);
    text-transform: uppercase;
    letter-spacing: 0.2px;
  }
  .person__title {
    margin: 6px 0 0;
    font-size: 19px;
    color: var(--text-dark);
    text-transform: uppercase;
  }
  .contact {
    position: absolute;
    right: 25px;
    top: 258px;
    margin: 0;
    padding: 0;
    list-style: none;
    color: var(--white);
    font-size: 18px;
    text-align: right;
  }
  .contact__item {
    display: flex;
    justify-content: flex-end;
    align-items: center;
    gap: 6px;
    height: 31px;
  }
  .contact__icon {
    width: 15px;
    height: 15px;
    fill: var(--white);
  }
  .address {
    position: absolute;
    right: 25px;
    top: 395px;
    margin: 0;
    color: var(--white);
    font-size: 18.5px;
    font-style: normal;
  }
  .web {
    position: absolute;
    left: 394px;
    top: 372px;
    margin: 0;
    color: var(--white);
    font-size: 23px;
    letter-spacing: 4px;
  }
  .web strong { font-weight: 700; }
</style>
</head>
<body>

<section class="card card--front" aria-label="Business card front">
  <svg class="card__art" viewBox="0 0 769 440" width="769" height="440" aria-hidden="true">
    <path fill="var(--navy)" d="M0,398 C260,425 570,300 769,14 L769,440 L0,440 Z"/>
    <path fill="var(--ink)" d="M0,318 C140,372 360,350 545,236 C360,350 160,395 0,372 Z"/>
  </svg>

  <div class="wordmark"><span class="wordmark__square"></span>Quayvale Lawyers</div>

  <div class="person">
    <h1 class="person__name">Paul Whitcombe</h1>
    <p class="person__title">Managing Partner</p>
  </div>

  <ul class="contact">
    <li class="contact__item">
      <svg class="contact__icon" viewBox="0 0 16 16"><path d="M3.5 1 6 4.5 4.6 6.2c.8 1.8 2.3 3.4 4.2 4.3L10.5 9 14 11.5 12.5 14.5C6.5 14.3 1.7 9.5 1.5 3.5Z"/></svg>
      <span>02 9364 2710(Main)</span>
    </li>
    <li class="contact__item">
      <svg class="contact__icon" viewBox="0 0 16 16"><path d="M3.5 1 6 4.5 4.6 6.2c.8 1.8 2.3 3.4 4.2 4.3L10.5 9 14 11.5 12.5 14.5C6.5 14.3 1.7 9.5 1.5 3.5Z"/></svg>
      <span>02 8472 3159(Direct)</span>
    </li>
    <li class="contact__item">
      <svg class="contact__icon" viewBox="0 0 16 16"><path d="M1 6 8 1.5 15 6V14H1Z M2.5 7 8 10.5 13.5 7 8 3.2Z" fill-rule="evenodd"/></svg>
      <span>paul@qvlegal.com.au</span>
    </li>
    <li class="contact__item">
      <svg class="contact__icon" viewBox="0 0 16 16"><path fill="none" stroke="#fff" stroke-width="1.3" d="M8 1.5a6.5 6.5 0 1 0 0 13 6.5 6.5 0 1 0 0-13M1.5 8h13M8 1.5c-3 3.5-3 9.5 0 13M8 1.5c3 3.5 3 9.5 0 13"/></svg>
      <span>www.qvlegal.com.au</span>
    </li>
  </ul>

  <address class="address">Level 9, 7 Ferris Lane, Sydney NSW 2000</address>
</section>

<section class="card card--back" aria-label="Business card back">
  <div class="wordmark"><span class="wordmark__square"></span>Quayvale Lawyers</div>
  <p class="web">www.<strong>qvlegal</strong>.com.au</p>
</section>

</body>
</html>
```